Road Construction Company needs business cards

We would like a new business card designed for our business.

We're a road construction company based in Qld, Australia.

Can the business card please have the following information on it.

Name: Warren Halbeck
Position: General Manager
Phone: 0472 915 348
Email: Warren.halbeck@tovrin.com.au
Address: 87 Marrow Ave, Pendlebay, QLD, 4023
Website: www.tovrin.com.au

Visually we'd like the card to be professional and simple.

Attached is our logo.

Our website is www.tovrin.com.au

Target Market(s)

Men aged 25-60

Contact Information for Business Card

As listed in project description

Font styles to use
Serif

Requirements
Must have
• Large logo on back of card

```html
<!DOCTYPE html>
<html lang="en">
<head>
<meta charset="utf-8">
<title>Tovrin Road Construction – Business Card</title>
<link rel="stylesheet" href="https://fonts.googleapis.com/css2?family=Inter:wght@400;700;800&display=swap">
<style>
  :root {
    --backdrop: #9d9d9d;
    --card-white: #ffffff;
    --brand-navy: #0b4f9e;
    --brand-deep: #1a3778;
    --brand-sky: #2ea3d9;
    --brand-mid: #2f6fb8;
    --ink-grey: #545454;
  }
  * { box-sizing: border-box; margin: 0; padding: 0; }
  html, body {
    width: 1021px; height: 1200px; overflow: hidden;
    background: var(--backdrop);
    font-family: "Inter", Arial, sans-serif;
  }
  .card {
    position: absolute; left: 138px;
    width: 745px; height: 426px;
    overflow: hidden;
  }
  .card--front { top: 121px; background: var(--brand-navy); }
  .card--back { top: 651px; background: var(--card-white); }

  .front-pattern {
    position: absolute; inset: 0;
    background: linear-gradient(135deg, var(--brand-deep) 0%, var(--brand-navy) 48%, var(--brand-mid) 100%);
  }
  .wordmark {
    position: absolute;
    font-weight: 800; line-height: 1; white-space: nowrap;
  }
  .tagline {
    position: absolute;
    font-weight: 800; font-size: 12px; line-height: 1; white-space: nowrap;
  }
  .card--front .wordmark { left: 386px; top: 289px; font-size: 58px; letter-spacing: 14px; color: var(--card-white); }
  .card--front .tagline { left: 388px; top: 344px; letter-spacing: 11.3px; color: var(--brand-sky); }

  .card--back .wordmark { left: 43px; top: 182px; font-size: 50px; letter-spacing: 14px; color: var(--brand-navy); }
  .card--back .tagline { left: 44px; top: 231px; letter-spacing: 10.6px; color: var(--brand-sky); }

  .divider {
    position: absolute; left: 375px; top: 102px;
    width: 2px; height: 224px; background: var(--brand-navy);
  }
  .contact { position: absolute; left: 394px; top: 100px; color: var(--ink-grey); }
  .contact__name { font-weight: 700; font-size: 27px; color: var(--brand-navy); letter-spacing: -0.3px; line-height: 1.1; }
  .contact__role { font-size: 20px; color: var(--brand-sky); margin-top: 3px; }
  .contact__address { font-size: 20px; line-height: 27px; margin-top: 20px; }
  .contact__lines { list-style: none; margin-top: 17px; font-size: 20px; line-height: 27px; }
  .contact__lines li { display: flex; align-items: center; gap: 6px; }
  .contact__lines svg { width: 18px; height: 18px; flex: none; }

  .footer-band { position: absolute; left: 0; bottom: 0; width: 745px; height: 15px; }
</style>
</head>
<body>
  <section class="card card--front" aria-label="Card front">
    <div class="front-pattern" role="img" aria-label="Repeating brand pattern in shades of blue"></div>
    <div class="wordmark">TOVRIN</div>
    <div class="tagline">ROAD CONSTRUCTION</div>
  </section>

  <section class="card card--back" aria-label="Card back">
    <div class="wordmark">TOVRIN</div>
    <div class="tagline">ROAD CONSTRUCTION</div>
    <div class="divider"></div>
    <div class="contact">
      <h1 class="contact__name">WARREN HALBECK</h1>
      <p class="contact__role">General Manager</p>
      <p class="contact__address">87 Marrow Ave<br>Pendlebay, QLD, 4023</p>
      <ul class="contact__lines">
        <li>
          <svg viewBox="0 0 24 24" aria-hidden="true"><path fill="#0b4f9e" d="M6.6 10.8a15.1 15.1 0 0 0 6.6 6.6l2.2-2.2c.3-.3.7-.4 1-.2 1.1.4 2.3.6 3.6.6.6 0 1 .4 1 1V20c0 .6-.4 1-1 1A17 17 0 0 1 3 4c0-.6.4-1 1-1h3.5c.6 0 1 .4 1 1 0 1.3.2 2.5.6 3.6.1.3 0 .7-.2 1z"/><path fill="none" stroke="#0b4f9e" stroke-width="2" d="M14 3a7 7 0 0 1 7 7M14 7a3 3 0 0 1 3 3"/></svg>
          0472 915 348
        </li>
        <li>
          <svg viewBox="0 0 24 24" aria-hidden="true"><rect x="3" y="6" width="18" height="13" fill="#0b4f9e"/><path d="M3 6l9 7 9-7" fill="none" stroke="#fff" stroke-width="1.6"/></svg>
          Warren.halbeck@tovrin.com.au
        </li>
        <li>
          <svg viewBox="0 0 24 24" aria-hidden="true"><circle cx="12" cy="12" r="9" fill="#0b4f9e"/><path d="M8 7c2 1 1 3 3 3s1 3-1 4M15 5c-1 2 1 3 2 4s2 3 0 5" fill="none" stroke="#fff" stroke-width="1.6"/></svg>
          www.tovrin.com.au
        </li>
      </ul>
    </div>
    <svg class="footer-band" viewBox="0 0 745 15" preserveAspectRatio="none" aria-hidden="true">
      <polygon points="0,0 398,0 385,15 0,15" fill="var(--brand-navy)"/>
      <polygon points="403,0 745,0 745,15 390,15" fill="var(--brand-sky)"/>
    </svg>
  </section>
</body>
</html>
```